Bramblewood Joinery Website

My client Bramblewood Joinery is looking for a redesign for a Word Press Website. Their current site is at www.bramblewoodjoinery.example They are a custom cabinet company, but also create bathroom, living room, bar and entertainment and bedroom cabinets too. They would like a design that emulates the master craftsman work they do yet a contemporary style.

Their current site was designed using Flash elements.

Target Market(s)

Home owners and builders of high end homes

Industry/Entity Type

Entertainment

Font styles to use
Serif
Decorative

Requirements
Must have
• Must show their work and logo using a contemporary style.
Nice to have
• Sliders that showcase their projects.

```html
<!DOCTYPE html>
<html lang="en">
<head>
<meta charset="utf-8">
<title>Bramblewood Joinery</title>
<link rel="stylesheet" href="https://fonts.googleapis.com/css2?family=Oswald:wght@500;700&family=Roboto:wght@400;500;700&display=swap">
<style>
:root{
  --green:#3ab03e;
  --green-dark:#2a8a2e;
  --footer:#1f4d22;
  --grey-band:#e9e9e9;
  --text:#333;
  --muted:#555;
  --white:#fff;
}
*{margin:0;padding:0;box-sizing:border-box}
html,body{width:1200px;height:2239px;overflow:hidden;background:var(--white);font-family:"Roboto",Arial,sans-serif;color:var(--text)}
.page{position:relative;width:1200px;height:2239px}
.abs{position:absolute}

/* top bar */
.topbar{left:0;top:0;width:1200px;height:40px;background:var(--green)}
.tagline{left:0;width:926px;top:11px;text-align:center;color:var(--white);font-size:14px;font-weight:700}
.topbar .socials{left:896px;top:9px;display:flex;gap:8px}
.dot-icon{width:20px;height:20px;border:1.5px solid var(--white);border-radius:50%}
.topbar .sep{left:1021px;top:12px;width:1px;height:16px;background:rgba(255,255,255,.7)}
.contact-link{left:1038px;top:12px;color:var(--white);font-size:13px}

/* nav */
.brand-badge{left:94px;top:40px;width:108px;height:110px;background:var(--green);border-radius:0 0 54px 54px/0 0 26px 26px;box-shadow:0 3px 6px rgba(0,0,0,.2);z-index:3;display:flex;flex-direction:column;align-items:center;justify-content:center;gap:6px}
.brand-badge .mark{width:22px;height:22px;border-radius:50%;background:var(--white)}
.brand-badge .name{color:var(--white);font-family:"Oswald",sans-serif;font-weight:500;font-size:13px;text-align:center;line-height:1.15}
.nav{left:252px;top:66px;display:flex;font-size:14px;color:var(--text)}
.nav a{color:inherit;text-decoration:none}
.nav .slash{margin:0 17px;color:#666}
.nav .current{color:var(--green);border-bottom:2px solid var(--green);padding-bottom:4px}

/* hero */
.hero{left:0;top:120px;width:1200px;height:522px;background:linear-gradient(135deg,#3b1f12 0%,#6e3a22 35%,#9a6a45 60%,#4a2a1a 100%)}
.hero-caption{left:212px;top:373px;width:673px;height:164px;background:rgba(40,30,25,.55);padding:22px 26px}
.hero-caption h1{font-family:"Oswald",sans-serif;font-weight:700;font-size:50px;color:var(--white);line-height:1;letter-spacing:.8px}
.hero-caption p{margin-top:14px;font-size:21px;color:var(--white);line-height:1.4;font-weight:500}
.hero-arrow{top:412px}
.hero-dots{left:972px;top:591px;display:flex;gap:10px}
.hero-dots span{width:16px;height:16px;border:2px solid var(--white);border-radius:50%;background:rgba(255,255,255,.2)}
.hero-dots span.on{background:var(--green)}

/* who we are */
.rule{left:94px;top:733px;width:82px;height:3px;background:var(--green)}
.who-mark{left:98px;top:750px;width:74px;height:74px;border-radius:50%;background:var(--green)}
.section-title{font-family:"Oswald",sans-serif;font-weight:700;font-size:30px;color:var(--green);line-height:1;letter-spacing:.3px}
.who-title{left:200px;top:731px}
.who-text{left:200px;top:778px;width:310px;font-size:15px;line-height:1.27;color:var(--text)}
.dash-curve{left:466px;top:690px}
.desc-box{left:570px;top:721px;width:536px;height:148px;background:var(--green);padding:22px 26px;color:var(--white)}
.desc-box h3{font-size:16px;font-weight:500;margin-bottom:8px}
.desc-box p{font-size:12.5px;line-height:1.5}
.desc-pointer{left:552px;top:797px;width:0;height:0;border-top:12px solid transparent;border-bottom:12px solid transparent;border-right:18px solid var(--green)}
.desc-plus{left:1082px;top:847px;width:24px;height:22px;background:#1b1b1b;color:var(--white);font-size:20px;line-height:22px;text-align:center;font-weight:700}

/* categories */
.band{left:0;top:1003px;width:1200px;height:724px;background:var(--grey-band)}
.cat{top:944px;width:140px;text-align:center}
.cat svg{display:block;margin:0 auto}
.cat .label{margin-top:20px;font-size:13.5px;font-weight:500;color:#222;letter-spacing:.2px;line-height:16px}
.cat.active .label{color:var(--green)}
.cat-underline{left:445px;top:1110px;width:134px;height:2px;background:var(--green)}
.cat-underline::after{content:"";position:absolute;left:60px;top:2px;border-left:7px solid transparent;border-right:7px solid transparent;border-top:7px solid var(--green)}

.t1{left:94px;top:1178px;width:325px;height:185px;background:linear-gradient(160deg,#c9ccd0,#6d5546)}
.t2{left:94px;top:1381px;width:325px;height:276px;background:linear-gradient(180deg,#f2f2f2,#7d8aa0)}
.t3{left:437px;top:1178px;width:324px;height:313px;background:var(--green)}
.t4{left:437px;top:1509px;width:324px;height:148px;background:linear-gradient(180deg,#e6e6e6,#555)}
.t5{left:779px;top:1178px;width:325px;height:185px;background:linear-gradient(160deg,#d7a46b,#7b4624)}
.t6{left:779px;top:1381px;width:325px;height:276px;background:linear-gradient(180deg,#e8e8e8,#b48a58)}
.t3 .zoom{position:absolute;left:124px;top:118px}

/* video */
.film{left:94px;top:1803px}
.video-title{left:200px;top:1799px}
.video-text{left:200px;top:1848px;width:445px;font-size:15.5px;line-height:1.22;color:var(--text)}
.screen{left:690px;top:1803px;width:417px;height:257px;background:linear-gradient(180deg,#2d2d2d,#1a1a1a);border-radius:10px 10px 4px 4px}
.screen-inner{position:absolute;left:14px;top:14px;right:14px;bottom:18px;background:var(--green)}
.screen .play{position:absolute;left:166px;top:76px}
.truck{left:370px;top:1970px;width:330px;height:97px;background:linear-gradient(90deg,#2f7a34,#e8e3d6 30%,#cfc4b0);border-radius:6px}

/* footer */
.footer{left:0;top:2142px;width:1200px;height:97px;background:var(--footer)}
.footer-text{left:94px;top:40px;font-size:13px;color:var(--white);white-space:nowrap}
.footer-text .bar{margin:0 20px}
.footer .socials{left:928px;top:33px;display:flex;gap:17px}
.footer .dot-icon{width:32px;height:32px;border-width:2px}
</style>
</head>
<body>
<div class="page">

  <header>
    <div class="abs topbar">
      <div class="abs tagline">Kansas City's Premier Custom Kitchen Cabinet Design Company</div>
      <div class="abs socials"><span class="dot-icon"></span><span class="dot-icon"></span><span class="dot-icon"></span><span class="dot-icon"></span></div>
      <div class="abs sep"></div>
      <a class="abs contact-link">Contact Us</a>
    </div>

    <div class="abs brand-badge">
      <span class="mark"></span>
      <span class="name">Bramblewood<br>Joinery</span>
    </div>

    <nav class="abs nav">
      <a class="current">Home</a><span class="slash">/</span>
      <a>Who We Are</a><span class="slash">/</span>
      <a>Getting Started</a><span class="slash">/</span>
      <a>Customer Experience</a><span class="slash">/</span>
      <a>Professional</a><span class="slash">/</span>
      <a>Portfolio</a><span class="slash">/</span>
      <a>Cabinet Hardware</a>
    </nav>
  </header>

  <section class="abs hero" role="img" aria-label="Photo of a custom wood kitchen with cherry cabinets, granite island and stainless fridge"></section>
  <div class="abs hero-caption">
    <h1>WE MAKE CUSTOM CABINET</h1>
    <p>Create Bathroom, Living Room, Bar &amp; Entertainment<br>&amp; Bedroom Cabinets</p>
  </div>
  <svg class="abs hero-arrow" style="left:166px" width="30" height="90" viewBox="0 0 30 90"><polyline points="26,2 4,45 26,88" fill="none" stroke="#fff" stroke-width="2"/></svg>
  <svg class="abs hero-arrow" style="left:955px" width="30" height="90" viewBox="0 0 30 90"><polyline points="4,2 26,45 4,88" fill="none" stroke="#3ab03e" stroke-width="2"/></svg>
  <div class="abs hero-dots"><span></span><span></span><span class="on"></span><span></span><span></span></div>

  <section>
    <div class="abs rule"></div>
    <div class="abs who-mark"></div>
    <h2 class="abs section-title who-title">WHO WE ARE</h2>
    <p class="abs who-text">Established in 1966, Bramblewood Joinery has long stood as one of the Midwest's most renowned makers of custom cabinets and fixtures.</p>
    <svg class="abs dash-curve" width="150" height="70" viewBox="0 0 150 70"><path d="M4 66 C30 20 90 10 144 24" fill="none" stroke="#555" stroke-width="1.2" stroke-dasharray="3 3"/><polyline points="136,19 145,24 137,30" fill="none" stroke="#555" stroke-width="1.2"/></svg>
    <div class="abs desc-pointer"></div>
    <div class="abs desc-box">
      <h3>DESCRIPTION</h3>
      <p>At Bramblewood Joinery, we've been designing and manufacturing the Midwest's finest custom cabinets and fixtures since 1966. From single cabinets to room remodels to entire home installations, our expert artisans help turn the house you live in to the home you've always dreamed of.</p>
    </div>
    <div class="abs desc-plus">+</div>
  </section>

  <section>
    <div class="abs band"></div>

    <div class="abs cat" style="left:91px">
      <svg width="136" height="119" viewBox="0 0 136 137" preserveAspectRatio="none"><polygon points="34,2 102,2 134,68 102,135 34,135 2,68" fill="#fff" stroke="#bbb" stroke-width="1.5"/><g fill="none" stroke="#777" stroke-width="2"><line x1="48" y1="92" x2="78" y2="60"/><ellipse cx="84" cy="52" rx="9" ry="12" transform="rotate(45 84 52)"/><line x1="88" y1="92" x2="56" y2="58"/><line x1="50" y1="52" x2="62" y2="64"/></g></svg>
      <div class="label">KITCHENS</div>
    </div>
    <div class="abs cat" style="left:267px">
      <svg width="136" height="119" viewBox="0 0 136 137" preserveAspectRatio="none"><polygon points="34,2 102,2 134,68 102,135 34,135 2,68" fill="#fff" stroke="#bbb" stroke-width="1.5"/><g fill="none" stroke="#777" stroke-width="2"><path d="M60 56 L80 46 L90 62 Z"/><line x1="80" y1="46" x2="90" y2="36"/><line x1="90" y1="36" x2="92" y2="92"/></g><g fill="#888"><circle cx="56" cy="68" r="1.6"/><circle cx="62" cy="74" r="1.6"/><circle cx="52" cy="80" r="1.6"/><circle cx="66" cy="84" r="1.6"/><circle cx="58" cy="90" r="1.6"/></g></svg>
      <div class="label">BATH</div>
    </div>
    <div class="abs cat active" style="left:442px">
      <svg width="136" height="119" viewBox="0 0 136 137" preserveAspectRatio="none"><polygon points="34,2 102,2 134,68 102,135 34,135 2,68" fill="#3ab03e"/><g fill="none" stroke="#fff" stroke-width="2.5"><rect x="52" y="50" width="14" height="42"/><rect x="66" y="40" width="18" height="52"/><polyline points="84,58 92,58 92,92"/><line x1="44" y1="92" x2="96" y2="92"/><line x1="72" y1="50" x2="72" y2="84"/><line x1="78" y1="50" x2="78" y2="84"/></g></svg>
      <div class="label">OFFICE</div>
    </div>
    <div class="abs cat" style="left:617px">
      <svg width="136" height="119" viewBox="0 0 136 137" preserveAspectRatio="none"><polygon points="34,2 102,2 134,68 102,135 34,135 2,68" fill="#fff" stroke="#bbb" stroke-width="1.5"/><g fill="none" stroke="#777" stroke-width="2"><rect x="42" y="40" width="52" height="54"/><line x1="59" y1="40" x2="59" y2="64"/><line x1="76" y1="40" x2="76" y2="64"/><line x1="42" y1="64" x2="94" y2="64"/><line x1="42" y1="78" x2="94" y2="78"/><line x1="68" y1="64" x2="68" y2="94"/></g></svg>
      <div class="label">CLOSET/DRESSING</div>
    </div>
    <div class="abs cat" style="left:793px">
      <svg width="136" height="119" viewBox="0 0 136 137" preserveAspectRatio="none"><polygon points="34,2 102,2 134,68 102,135 34,135 2,68" fill="#fff" stroke="#bbb" stroke-width="1.5"/><g fill="none" stroke="#777" stroke-width="2"><polyline points="40,66 68,40 96,66"/><polyline points="48,60 48,92 88,92 88,60"/><line x1="58" y1="82" x2="78" y2="62"/><line x1="58" y1="62" x2="78" y2="82"/></g></svg>
      <div class="label">WORKSHOP</div>
    </div>
    <div class="abs cat" style="left:967px">
      <svg width="136" height="119" viewBox="0 0 136 137" preserveAspectRatio="none"><polygon points="34,2 102,2 134,68 102,135 34,135 2,68" fill="#fff" stroke="#bbb" stroke-width="1.5"/><g fill="none" stroke="#777" stroke-width="2"><rect x="40" y="44" width="56" height="46"/><path d="M40 44 Q52 62 44 90"/><path d="M96 44 Q84 62 92 90"/><polygon points="68,56 71,64 79,64 73,69 75,77 68,72 61,77 63,69 57,64 65,64"/></g></svg>
      <div class="label">ENTERTAINMENT</div>
    </div>
    <div class="abs cat-underline"></div>

    <div class="abs t1" role="img" aria-label="Executive office with curved wood desk and dark shelving"></div>
    <div class="abs t2" role="img" aria-label="Open office with rows of blue chairs and partitions"></div>
    <div class="abs t3" role="img" aria-label="Bright office with built-in shelving, shown under a green highlight">
      <svg class="zoom" width="76" height="76" viewBox="0 0 76 76"><circle cx="38" cy="38" r="36" fill="none" stroke="#fff" stroke-width="2"/><line x1="38" y1="24" x2="38" y2="52" stroke="#fff" stroke-width="2"/><line x1="24" y1="38" x2="52" y2="38" stroke="#fff" stroke-width="2"/></svg>
    </div>
    <div class="abs t4" role="img" aria-label="Loft office with white roof trusses and desks"></div>
    <div class="abs t5" role="img" aria-label="Warm wood office desk with leather chair"></div>
    <div class="abs t6" role="img" aria-label="Large open-plan office with wooden workstations"></div>
  </section>

  <section>
    <svg class="abs film" width="82" height="90" viewBox="0 0 82 90"><rect x="0" y="0" width="82" height="3" fill="#3ab03e"/><rect x="2" y="14" width="78" height="74" fill="none" stroke="#3ab03e" stroke-width="4"/><g fill="#3ab03e"><rect x="6" y="18" width="6" height="6"/><rect x="6" y="78" width="6" height="6"/><rect x="70" y="18" width="6" height="6"/><rect x="70" y="78" width="6" height="6"/><rect x="18" y="18" width="6" height="6"/><rect x="58" y="18" width="6" height="6"/><rect x="18" y="78" width="6" height="6"/><rect x="58" y="78" width="6" height="6"/><polygon points="33,36 54,51 33,66"/></g></svg>
    <h2 class="abs section-title video-title">WATCH OUR VIDEO</h2>
    <p class="abs video-text">At Bramblewood Joinery, we've been designing and manufacturing the Midwest's finest custom cabinets and fixtures since 1966. From single cabinets to room remodels to entire home installations, our expert artisans help turn the house you live in to the home you've always dreamed of</p>
    <div class="abs screen" role="img" aria-label="Video player showing the company introduction film">
      <div class="screen-inner"></div>
      <svg class="play" width="80" height="80" viewBox="0 0 80 80"><circle cx="40" cy="40" r="38" fill="none" stroke="#fff" stroke-width="2.5"/><polygon points="32,26 56,40 32,54" fill="#fff"/></svg>
    </div>
    <div class="abs truck" role="img" aria-label="Illustration of the company delivery truck"></div>
  </section>

  <footer class="abs footer">
    <div class="abs footer-text">Copyright © 2015 All Rights Reserved<span class="bar">|</span>Powered by bramblewoodjoinery.example, LLC</div>
    <div class="abs socials"><span class="dot-icon"></span><span class="dot-icon"></span><span class="dot-icon"></span><span class="dot-icon"></span></div>
  </footer>

</div>
</body>
</html>
```